Coastline Premier Retreats Business Card Design

Design a business card for Coastline Premier Retreats. Look at the website for colors and reference. Card should have logo, name, title, office number, mobile number, email, URL and a tagline like, "Luxury Hotel & Resort Email Marketing" (This might change).

https://www.coastlinepremierretreats.example

The rest I will leave up to your imagination.

Contact Information for Business Card

Logo, name, title, office number, mobile number, email, URL and a tagline like, "Luxury Hotel & Resort Email Marketing" (This might change).

```html
<!DOCTYPE html>
<html lang="en">
<head>
<meta charset="utf-8">
<title>Coastline Premier Retreats – Business Card</title>
<link href="https://fonts.googleapis.com/css2?family=Open+Sans:wght@400;600;700&display=swap" rel="stylesheet">
<style>
  :root {
    --backdrop: #222224;
    --card: #1f1f23;
    --card-back: #1c1c20;
    --emboss: #2a2a2f;
    --orange: #f47521;
    --white: #ffffff;
    --rule: #8a8a90;
  }
  * { box-sizing: border-box; margin: 0; padding: 0; }
  html, body {
    width: 1200px; height: 780px; overflow: hidden;
    background: var(--backdrop);
    font-family: "Open Sans", Arial, sans-serif;
  }
  .canvas { position: relative; width: 1200px; height: 780px; }
  .card {
    position: absolute; top: 236px;
    width: 560px; height: 308px;
    box-shadow: 0 18px 40px rgba(0,0,0,.55);
    overflow: hidden;
  }
  .card--front { left: 30px; background: var(--card); }
  .card--back { left: 610px; background: var(--card-back); }

  .brand {
    position: absolute; left: 34px; top: 44px;
    display: flex; align-items: center; gap: 10px;
  }
  .brand__mark { width: 14px; height: 14px; background: var(--orange); flex: none; }
  .brand__name {
    color: var(--white); font-weight: 700; font-size: 14px;
    letter-spacing: .06em; text-transform: uppercase; line-height: 1.25;
    width: 180px;
  }
  .divider { position: absolute; left: 0; top: 0; }

  .person { position: absolute; left: 270px; top: 62px; white-space: nowrap; }
  .person__name { font-size: 25px; font-weight: 700; color: var(--white); line-height: 1.1; }
  .person__first { color: var(--orange); }
  .person__title { font-size: 13px; color: var(--white); margin-top: 4px; }

  .contacts { position: absolute; left: 270px; top: 138px; list-style: none; }
  .contacts li {
    display: flex; align-items: center; gap: 9px;
    color: var(--white); font-size: 12px; line-height: 22px;
    white-space: nowrap;
  }
  .contacts svg { width: 13px; height: 13px; flex: none; }

  .tagline-band {
    position: absolute; left: 0; bottom: 0; width: 100%; height: 38px;
    background: var(--orange); display: flex; align-items: center;
    padding-left: 34px;
    color: var(--white); font-size: 13px;
  }

  .back-brand {
    position: absolute; inset: 0;
    display: flex; align-items: center; justify-content: center;
    color: var(--emboss); font-weight: 700; font-size: 30px;
    letter-spacing: .08em; text-transform: uppercase; text-align: center;
    line-height: 1.2;
  }
</style>
</head>
<body>
<main class="canvas">
  <section class="card card--front" aria-label="Business card front">
    <div class="brand">
      <span class="brand__mark"></span>
      <span class="brand__name">Coastline Premier Retreats</span>
    </div>

    <svg class="divider" width="560" height="308" aria-hidden="true">
      <line x1="258" y1="52" x2="212" y2="250" stroke="var(--rule)" stroke-width="1"/>
    </svg>

    <div class="person">
      <h1 class="person__name"><span class="person__first">Marta</span> Kovalenko</h1>
      <p class="person__title">Co-Founder</p>
    </div>

    <ul class="contacts">
      <li>
        <svg viewBox="0 0 16 16" aria-hidden="true"><path fill="var(--orange)" d="M3.6 1.2l2.2 2.6-1.3 1.7c.8 1.9 2.3 3.4 4.2 4.2l1.7-1.3 2.6 2.2-1.2 2.6C6.9 13.8 2.2 9.1 1 4.3z"/></svg>
        (555) 210-4836
      </li>
      <li>
        <svg viewBox="0 0 16 16" aria-hidden="true"><rect x="4" y="1" width="8" height="14" rx="1.5" fill="none" stroke="var(--orange)" stroke-width="1.5"/><circle cx="8" cy="12.5" r=".9" fill="var(--orange)"/></svg>
        (555) 318-6420
      </li>
      <li>
        <svg viewBox="0 0 16 16" aria-hidden="true"><circle cx="8" cy="8" r="6.5" fill="none" stroke="var(--orange)" stroke-width="1.4"/><ellipse cx="8" cy="8" rx="2.8" ry="6.5" fill="none" stroke="var(--orange)" stroke-width="1.2"/><line x1="1.5" y1="8" x2="14.5" y2="8" stroke="var(--orange)" stroke-width="1.2"/></svg>
        www.coastlinepremierretreats.example
      </li>
      <li>
        <svg viewBox="0 0 16 16" aria-hidden="true"><rect x="1" y="3" width="14" height="10" rx="1" fill="var(--orange)"/><path d="M1.5 3.5L8 9l6.5-5.5" fill="none" stroke="var(--card)" stroke-width="1.3"/></svg>
        info@coastlinepremierretreats.example
      </li>
    </ul>

    <div class="tagline-band">Luxury Hotel &amp; Resort Email Marketing</div>
  </section>

  <section class="card card--back" aria-label="Business card back">
    <p class="back-brand">Coastline<br>Premier Retreats</p>
  </section>
</main>
</body>
</html>
```